Visitenkartenvorlage ändern
Zielgruppe
Eventmanagement
Aufgabenstellung
Die beiliegende Visitenkarte wäre das "perfekte" Logo für mich. Da es sich hierbei aber um eine Vorlage eines Online-Druck-Anbieters handelt, darf es leider nur für deren Drucke verwendet werden und nicht für Printwerbung, Homepage etc. Daher sollte es genügend verfremdet werden, so dass ich es verwenden kann.

```html
<!DOCTYPE html>
<html lang="de">
<head>
<meta charset="utf-8">
<title>Lumen Events – Visitenkarte</title>
<link rel="stylesheet" href="https://fonts.googleapis.com/css2?family=Hind:wght@300;400&family=Pinyon+Script&display=swap">
<style>
  :root {
    --page-bg: #e6e6e6;
    --card-base: #ac5ea2;
    --card-edge: #8f4886;
    --ink: #ffffff;
    --ornament: #f3e4f0;
    --band: rgba(255, 255, 255, 0.55);
  }
  * { margin: 0; padding: 0; box-sizing: border-box; }
  html, body {
    width: 1163px; height: 1200px; overflow: hidden;
    background: var(--page-bg);
  }
  .canvas { position: relative; width: 1163px; height: 1200px; }
  .card {
    position: absolute; left: 249px; width: 698px; height: 400px;
    background: radial-gradient(ellipse at center, var(--card-base) 60%, var(--card-edge) 130%);
    color: var(--ink);
    font-family: "Hind", "Helvetica Neue", Arial, sans-serif;
    font-weight: 300;
  }
  .card--front { top: 163px; }
  .card--back { top: 658px; }
  .card > * { position: absolute; }
  .centered { left: 0; right: 0; text-align: center; }
  .brand-name {
    font-size: 25px; letter-spacing: 4px; line-height: 1;
  }
  .tagline {
    font-size: 18px; letter-spacing: 2.5px; font-variant: small-caps; line-height: 1;
  }
  .web { font-size: 16px; letter-spacing: 0.6px; line-height: 1; }
  .ornament { display: block; }
  .person {
    font-family: "Pinyon Script", "Brush Script MT", cursive;
    font-size: 38px; line-height: 1; opacity: 0.95;
  }
  .contact { font-size: 16px; letter-spacing: 2px; line-height: 1; }
  .contact--mail { left: 59px; }
  .contact--phone { right: 55px; letter-spacing: 1px; font-size: 18px; }
</style>
</head>
<body>
<main class="canvas">

  <section class="card card--front" aria-label="Vorderseite">
    <p class="brand-name centered" style="top:239px;top:75px">LUMEN EVENTS</p>
    <svg class="ornament" style="left:234px; top:149px" width="230" height="98" role="img" aria-label="Symmetrisches florales Ornament">
      <rect width="230" height="98" rx="18" fill="var(--ornament)" opacity="0.85"/>
    </svg>
    <p class="tagline centered" style="top:296px">Events und mehr</p>
    <p class="web centered" style="top:327px">WWW.LUMEN-EVENTS.DE</p>
  </section>

  <section class="card card--back" aria-label="Rückseite">
    <svg class="ornament" style="left:279px; top:26px" width="142" height="68" role="img" aria-label="Symmetrisches florales Ornament">
      <rect width="142" height="68" rx="14" fill="var(--ornament)" opacity="0.85"/>
    </svg>
    <svg class="ornament" style="left:11px; top:85px" width="676" height="8" role="img" aria-label="Verzierte Zierlinie">
      <rect x="0" y="2" width="290" height="4" rx="2" fill="var(--band)"/>
      <rect x="386" y="2" width="290" height="4" rx="2" fill="var(--band)"/>
    </svg>
    <p class="brand-name centered" style="top:141px">LUMEN EVENTS</p>
    <p class="tagline centered" style="top:190px">Events und mehr</p>
    <p class="person centered" style="top:240px">Carla Brunelli</p>
    <p class="contact contact--mail" style="top:342px">info@lumen-events.de</p>
    <p class="contact contact--phone" style="top:340px">+ 49 170 5550123</p>
  </section>

</main>
</body>
</html>
```